Graphic Design Zephyrmart Book Description

There is a book on Zephyrmart that is my competitor that has a large graphic design as part of the description for the book and I want a similar thing for my book to make it stand out more.

My competitors book is here: https://www.zephyrmart.example/Stellar-Chemistry-Novices-Grasping-Walkthrough/dp/K47RTPW612/

My book is here: https://www.zephyrmart.example/Stellar-Chemistry-Groundwork-Reactions-Bonding/dp/K9HXCVT27S/

You can see the kind of thing I am looking for on the book listing but I have attached an image below.

Thanks

Trevor

```html
<!DOCTYPE html>
<html lang="en">
<head>
<meta charset="utf-8">
<title>Stellar Chemistry – Book Description Graphic</title>
<link rel="stylesheet" href="https://fonts.googleapis.com/css2?family=Bebas+Neue&family=Oswald:wght@300;600&family=Poppins:wght@400;500;800;900&display=swap">
<style>
:root{
  --space-deep:#0d1320;
  --space-mid:#2a2f3c;
  --space-warm:#5a4a38;
  --earth-blue:#3e6f9e;
  --yellow:#f4e71d;
  --yellow-deep:#d8c90e;
  --navy:#0b2a8a;
  --glow:#39c6ff;
  --red:#e0161b;
  --red-dark:#a80c10;
  --white:#ffffff;
  --ink:#1b1b1b;
  --panel:#121c44;
}
*{box-sizing:border-box;margin:0;padding:0}
html,body{width:723px;height:1200px;overflow:hidden;background:var(--white)}
.canvas{position:relative;width:723px;height:1200px;overflow:hidden;
  background:linear-gradient(180deg,var(--white) 0 60%,#eef0f8 100%);
  font-family:'Poppins',sans-serif;color:var(--ink)}
.hero-bg{position:absolute;left:0;top:0;width:723px;height:457px;
  background:radial-gradient(ellipse 70% 40% at 45% 8%,var(--space-warm),transparent 70%),
  radial-gradient(ellipse 90% 35% at 50% 105%,var(--earth-blue),transparent 70%),
  linear-gradient(180deg,var(--space-mid),var(--space-deep) 60%,#1d3550)}
.headline{position:absolute;left:368px;top:44px;width:350px;font-weight:400}
.headline .lead{font-family:'Bebas Neue',sans-serif;font-size:66px;line-height:.88;color:var(--white)}
.headline .accent{font-weight:800;font-size:31px;color:var(--yellow);line-height:.98;margin-top:4px}
.headline .realm{font-weight:800;font-size:30px;color:var(--white);line-height:1.1;margin-top:2px}
.headline .title{font-weight:900;font-size:42px;color:var(--navy);line-height:1;
  text-shadow:0 0 6px var(--glow),0 0 2px var(--glow);margin-top:2px}
.mockup{position:absolute}
.mockup-stack{left:79px;top:85px;width:254px;height:300px;
  background:linear-gradient(100deg,#c9bb10,var(--yellow) 30%,#eedf1a)}
.mockup-open{left:195px;top:330px;width:300px;height:200px;
  background:linear-gradient(170deg,#fafafa,#d9dadf);transform:skewY(-6deg)}
.mockup-back{left:522px;top:345px;width:148px;height:200px;
  background:linear-gradient(100deg,#e6d815,var(--yellow))}
.seal{position:absolute;left:50px;top:377px;width:170px;height:155px}
.seal-text{position:absolute;left:50px;top:413px;width:170px;text-align:center;
  font-size:11.5px;line-height:1.15;color:var(--white);font-weight:800}
.seal-text .thin{font-weight:400;letter-spacing:2px;font-size:12px}
.seal-text .hl{color:var(--yellow)}
.sticker{position:absolute;left:594px;top:268px;width:96px;height:96px;border-radius:50%;
  background:radial-gradient(circle at 40% 35%,#f2343a,var(--red) 55%,var(--red-dark));
  box-shadow:0 3px 6px rgba(0,0,0,.35);transform:rotate(18deg);
  text-align:center;color:var(--white);padding-top:16px}
.sticker .small{font-weight:800;font-size:8px;line-height:1.1}
.sticker .big{font-family:'Bebas Neue',sans-serif;font-size:19px;line-height:.85;color:var(--yellow)}
.features{position:absolute;left:40px;top:573px;width:644px;height:274px;border-radius:18px;
  background:radial-gradient(ellipse at 50% 60%,#3a3f8a,var(--panel) 70%)}
.feature{position:absolute;top:12px;width:142px;height:247px;border-radius:10px;overflow:hidden;
  background:linear-gradient(180deg,var(--white),#eae6f6)}
.feature-head{height:108px;background:linear-gradient(160deg,#fff36a,var(--yellow) 40%,var(--yellow-deep));
  border-bottom:2px solid #2a2a2a;border-radius:10px 10px 12px 12px;
  display:flex;flex-direction:column;justify-content:center;align-items:center;text-align:center;
  font-family:'Oswald',sans-serif;color:var(--ink);line-height:1}
.feature-head .light{font-weight:300;font-size:20px}
.feature-head .bold{font-weight:600;font-size:20px}
.feature-body{padding:12px 6px 0;text-align:center;font-size:12.5px;line-height:1.25}
.f1{left:19px}.f2{left:174px}.f3{left:329px}.f4{left:484px}
.mockup-single{left:44px;top:880px;width:200px;height:285px;transform:rotate(-4deg);
  background:linear-gradient(100deg,#cfc012,var(--yellow) 20%,#f0e01a)}
.find-banner{position:absolute;left:230px;top:883px;width:450px;height:41px;background:var(--ink);
  border-radius:0 8px 8px 0;color:var(--white);font-size:21px;letter-spacing:1px;
  display:flex;align-items:center;padding-left:43px;font-weight:400}
.find-banner b{font-weight:800;margin-left:7px}
.contents{position:absolute;left:275px;top:944px;list-style:none}
.contents li{display:table;border:1.5px solid var(--yellow);border-radius:10px;padding:0 24px 0 13px;
  height:19px;line-height:16px;font-size:12.5px;font-weight:500;color:#2b2b2b;margin-bottom:8.4px;background:var(--white)}
</style>
</head>
<body>
<main class="canvas">
  <div class="hero-bg" role="img" aria-label="Starfield and night-side Earth seen from orbit"></div>

  <div class="mockup mockup-stack" role="img" aria-label="Two yellow paperback copies of Stellar Chemistry by Elias Hartwell, standing"></div>
  <div class="mockup mockup-open" role="img" aria-label="Open book showing the introduction and chapter one pages"></div>
  <div class="mockup mockup-back" role="img" aria-label="Yellow back cover with blurb text"></div>

  <h1 class="headline">
    <div class="lead">EMBARK ON A</div>
    <div class="accent">MIND-BENDING<br>JOURNEY</div>
    <div class="realm">INTO THE REALM OF</div>
    <div class="title">STELLAR<br>CHEMISTRY</div>
  </h1>

  <svg class="seal" viewBox="0 0 100 100" preserveAspectRatio="none" aria-hidden="true">
    <defs><radialGradient id="sealFill" cx="45%" cy="40%"><stop offset="0" stop-color="#f22a30"/><stop offset="1" stop-color="#b80d12"/></radialGradient></defs>
    <path fill="url(#sealFill)" d="M50 2 L58 11 L70 6 L74 18 L87 18 L86 31 L97 38 L90 49 L97 61 L86 68 L87 81 L74 82 L70 94 L58 89 L50 98 L42 89 L30 94 L26 82 L13 81 L14 68 L3 61 L10 49 L3 38 L14 31 L13 18 L26 18 L30 6 L42 11 Z"/>
  </svg>
  <div class="seal-text">
    <div class="thin">IDEAL FOR</div>
    <div class="thin">IDEAL FOR</div>
    <div class="hl">SCIENCE STUDENTS,</div>
    <div>CHEMISTRY</div>
    <div>AND LAB</div>
    <div>ENTHUSIASTS</div>
  </div>

  <div class="sticker">
    <div class="small">PERFECT<br>GIFT FOR THE</div>
    <div class="big">SCIENCE<br>LOVER</div>
  </div>

  <section class="features">
    <article class="feature f1">
      <div class="feature-head"><span class="light">HISTORY</span><span class="bold">OF MODERN<br>CHEMISTRY</span></div>
      <p class="feature-body">Explore the fascinating history of chemistry and the brilliant minds behind its greatest discoveries</p>
    </article>
    <article class="feature f2">
      <div class="feature-head"><span class="light">FUNDAMENTAL</span><span class="bold">PRINCIPLES OF<br>ATOMIC BONDS</span></div>
      <p class="feature-body">Grasp the fundamental principles of atomic structure, chemical bonding, and the periodic table</p>
    </article>
    <article class="feature f3">
      <div class="feature-head"><span class="light">CHEMICAL</span><span class="bold">REACTIONS</span></div>
      <p class="feature-body">Dive into the dynamic world of chemical reactions, energy changes and what makes matter transform</p>
    </article>
    <article class="feature f4">
      <div class="feature-head"><span class="light">CHEMISTRY</span><span class="bold">IN EVERYDAY<br>LIFE</span></div>
      <p class="feature-body">Learn about the practical applications of chemistry, from medicine and materials to the food we eat</p>
    </article>
  </section>

  <div class="mockup mockup-single" role="img" aria-label="Yellow paperback cover of Stellar Chemistry: The Groundwork of Reactions and Bonding by Elias Hartwell"></div>

  <h2 class="find-banner">IN THIS BOOK <b>YOU WILL FIND</b></h2>
  <ul class="contents">
    <li>The Chemical World Unveiled</li>
    <li>The Mathematical Symphony of Atoms and Molecules</li>
    <li>Beyond the Periodic Table</li>
    <li>Chemistry at Work</li>
    <li>Bridging Chemical Reactions and Bonding</li>
    <li>Chemical Paradoxes and Classic Experiments</li>
    <li>Chemistry for the Curious Mind</li>
    <li>Chemistry Demystified - A Practical Guide</li>
  </ul>
</main>
</body>
</html>
```